We are a local Communty Pharmacy wishing to promote and market a specialised Pharmaceutical Service

We would like a design that is professional and enticing ( according to the brief In attached files)
We wish to Market Compounding Pharmacy as a specialist side of our business.
We have the expertise a purpose built preparation laboratory.
The main purpose is an Internet presence that entices prospective patients to contact or visit our physical store.

Target Market(s)

Patients Medicos and Veterinary clients

Industry/Entity Type

Pharmacy

Coding

Coded - Design and coding required

Number of Pages Required

1 page

Requirements
Must have
• Clear friendly image
Nice to have
• soft enticing feel
Should not have
• No crass loud unprofessional elements

```html
<!DOCTYPE html>
<html lang="en">
<head>
<meta charset="utf-8">
<title>Larkfield Chemists</title>
<link rel="stylesheet" href="https://fonts.googleapis.com/css2?family=Open+Sans:wght@300;400;600;700&display=swap">
<style>
:root{
  --teal:#3bb3d6;
  --teal-dark:#2b9ec2;
  --sky:#8fd3ec;
  --pink:#e58ac4;
  --lime:#c9dd62;
  --lilac:#b8a0d8;
  --ink:#4a4f55;
  --muted:#8a9096;
  --pale:#eef4f7;
  --white:#ffffff;
}
*{margin:0;padding:0;box-sizing:border-box}
html,body{width:776px;height:1200px;overflow:hidden}
body{font-family:"Open Sans",Arial,sans-serif;color:var(--ink);background:var(--white);font-size:9px;line-height:1.5;position:relative}
.site-header{height:32px;display:flex;align-items:center;justify-content:space-between;padding:0 104px}
.brand{color:var(--ink);font-weight:600;font-size:11px;letter-spacing:.3px}
.main-nav{display:flex;align-items:center;gap:4px}
.main-nav a{font-size:7px;color:var(--muted);text-decoration:none;padding:4px 9px;letter-spacing:.5px}
.main-nav a.active{background:var(--pale);color:var(--teal)}
.nav-search{width:18px;height:18px;border-radius:50%;background:var(--teal);margin-left:6px}
.hero{position:relative;height:343px;background:linear-gradient(100deg,#8fc3cf 0%,#b9dbe0 45%,#e4eef0 70%,#d8e4e8 100%);overflow:hidden}
.hero-photo{position:absolute;right:104px;top:0;width:250px;height:343px;background:linear-gradient(180deg,#d9c2ad 0%,#e9e1da 45%,#f4f4f4 100%);opacity:.85}
.hero-copy{position:absolute;left:104px;top:150px;width:330px}
.hero-copy h1{font-weight:300;font-size:13px;line-height:1.45;color:var(--white);letter-spacing:.6px}
.hero-copy h1 strong{font-weight:700}
.btn{display:inline-block;background:var(--teal);color:var(--white);font-size:7px;padding:6px 12px;border-radius:2px;letter-spacing:.5px;text-decoration:none}
.hero-copy .btn{margin-top:16px}
.hero-arrow{position:absolute;left:34px;top:160px;width:14px;height:14px;border-radius:50%;background:rgba(255,255,255,.55)}
.services{display:flex;gap:12px;padding:20px 104px 0}
.service{flex:1;height:104px;color:var(--white);text-align:center;padding-top:20px}
.service svg{width:34px;height:34px;display:block;margin:0 auto 8px}
.service h3{font-size:7.5px;font-weight:600}
.service p{font-size:6px;opacity:.85}
.s-sky{background:var(--sky)}.s-pink{background:var(--pink)}.s-lime{background:var(--lime)}.s-lilac{background:var(--lilac)}
.about{display:flex;gap:26px;padding:46px 104px 0}
.about-text{flex:1}
.about h2{color:var(--teal);font-weight:300;font-size:17px;letter-spacing:.5px;margin-bottom:14px}
.about p{font-size:6.5px;color:var(--muted);margin-bottom:10px}
.about .btn{margin-top:6px}
.about-photo{width:196px;height:138px;margin-top:30px;background:linear-gradient(135deg,#d5e8ee,#f1f4f5 60%,#e6d3c8)}
.products{position:absolute;left:0;top:753px;width:776px;height:283px;background:var(--pale)}
.products-tab{position:absolute;left:50%;top:-14px;transform:translateX(-50%);background:var(--teal);color:var(--white);font-size:14px;font-weight:300;padding:4px 46px;border-radius:14px 14px 0 0;white-space:nowrap}
.product-grid{display:flex;gap:22px;padding:46px 104px 0}
.product{flex:1;text-align:center}
.product-img{height:100px;background:var(--white);border:1px solid #dfe6ea;padding:10px}
.product-img div{height:100%;background:linear-gradient(135deg,#f4f7fb,#cfe2f0 60%,#e8b7c9)}
.product h4{font-size:7px;font-weight:700;margin-top:10px}
.product p{font-size:6px;color:var(--muted);margin:3px 0 6px}
.product .more{font-size:6px;color:var(--teal)}
.site-footer{position:absolute;left:0;top:1036px;width:776px;height:164px;background:var(--teal);color:var(--white);padding:22px 104px 0}
.footer-cols{display:flex;gap:30px}
.footer-cols h5{font-size:8px;font-weight:600;margin-bottom:6px}
.footer-cols li{list-style:none;font-size:6px;opacity:.85;line-height:1.8}
.col-links{width:80px}.col-products{width:90px}
.map{width:150px;height:70px;background:linear-gradient(135deg,#e4ecd9,#f2f2ea 50%,#d7e5ee)}
.col-news p{font-size:6px;opacity:.85;margin-bottom:6px}
.email{width:130px;height:16px;background:var(--white);color:var(--muted);font-size:6px;padding:3px 6px;margin-bottom:6px}
.subscribe{background:var(--teal-dark);border:1px solid rgba(255,255,255,.6)}
.footer-bottom{display:flex;justify-content:space-between;align-items:center;margin-top:14px;font-size:6px;opacity:.9}
.social{display:flex;gap:6px}
.social span{width:16px;height:16px;border-radius:50%;background:rgba(255,255,255,.3)}
</style>
</head>
<body>
<header class="site-header">
  <div class="brand">Larkfield Chemists</div>
  <nav class="main-nav">
    <a class="active" href="#">HOME</a><a href="#">ABOUT US</a><a href="#">COMPOUNDS</a><a href="#">PHARMACY</a><a href="#">CONTACT</a>
    <span class="nav-search"></span>
  </nav>
</header>

<section class="hero">
  <div class="hero-photo" role="img" aria-label="Smiling pharmacist in glasses and white coat at pharmacy shelves"></div>
  <span class="hero-arrow"></span>
  <div class="hero-copy">
    <h1>TO PROVIDE AN AWARENESS OF WHAT WE ARE, THAT WE ARE IN THE SPECIALITY BUSINESS OF COMPOUNDING PHARMACY ... <strong>AND WE WANT PEOPLE TO CONTACT</strong></h1>
    <a class="btn" href="#">VISIT OUR PHARMACY STORE</a>
  </div>
</section>

<section class="services">
  <div class="service s-sky">
    <svg viewBox="0 0 34 34" fill="none" stroke="#fff" stroke-width="2"><rect x="7" y="8" width="20" height="18" rx="2"/><path d="M17 12v10M12 17h10"/></svg>
    <h3>We Are Compounding</h3><p>Prepared to your needs</p>
  </div>
  <div class="service s-pink">
    <svg viewBox="0 0 34 34" fill="none" stroke="#fff" stroke-width="2"><path d="M6 16h22a11 9 0 0 1-22 0z"/><path d="M20 16l8-10"/></svg>
    <h3>Expert Service</h3><p>Skilled local team</p>
  </div>
  <div class="service s-lime">
    <svg viewBox="0 0 34 34" fill="none" stroke="#fff" stroke-width="2"><rect x="10" y="10" width="14" height="18" rx="2"/><rect x="12" y="5" width="10" height="5"/></svg>
    <h3>Own Laboratory</h3><p>Purpose built facility</p>
  </div>
  <div class="service s-lilac">
    <svg viewBox="0 0 34 34" fill="none" stroke="#fff" stroke-width="2"><rect x="4" y="11" width="18" height="13"/><path d="M22 15h5l3 4v5h-8"/><circle cx="10" cy="26" r="2.5"/><circle cx="25" cy="26" r="2.5"/></svg>
    <h3>Home Delivery</h3><p>To your door</p>
  </div>
</section>

<section class="about">
  <div class="about-text">
    <h2>WHAT IS COMPOUNDING PHARMACY?</h2>
    <p>Compounding is the preparation of a medicine made specially for one patient. Our pharmacists combine, mix or alter ingredients to create a treatment that suits the exact strength, form and flavour a person needs, when a standard product is not the right fit.</p>
    <p>We work closely with doctors, specialists and veterinarians to prepare creams, capsules, liquids and lozenges in our purpose built laboratory. Every preparation is made with care, tested for quality and explained clearly, so patients and pets receive a medicine they can take with confidence. Talk to our team or visit our store today.</p>
    <a class="btn" href="#">Read More</a>
  </div>
  <div class="about-photo" role="img" aria-label="Pharmacist holding a prescription bottle in the dispensary"></div>
</section>

<section class="products">
  <div class="products-tab">Products &amp; Services</div>
  <div class="product-grid">
    <div class="product"><div class="product-img"><div role="img" aria-label="Boxed medicine product"></div></div><h4>PRODUCT NAME</h4><p>Short product note here for the item shown.</p><span class="more">READ MORE</span></div>
    <div class="product"><div class="product-img"><div role="img" aria-label="Medicine bottle and box"></div></div><h4>PRODUCT NAME</h4><p>Short product note here for the item shown.</p><span class="more">READ MORE</span></div>
    <div class="product"><div class="product-img"><div role="img" aria-label="Tablet pack product"></div></div><h4>PRODUCT NAME</h4><p>Short product note here for the item shown.</p><span class="more">READ MORE</span></div>
    <div class="product"><div class="product-img"><div role="img" aria-label="Boxed supplement product"></div></div><h4>PRODUCT NAME</h4><p>Short product note here for the item shown.</p><span class="more">READ MORE</span></div>
  </div>
</section>

<footer class="site-footer">
  <div class="footer-cols">
    <div class="col-links"><h5>Links</h5><ul><li>Home</li><li>About Us</li><li>Compounds</li><li>Pharmacy</li><li>Contact</li></ul></div>
    <div class="col-products"><h5>Products</h5><ul><li>Creams and gels</li><li>Capsules</li><li>Oral liquids</li><li>Veterinary care</li><li>Lozenges</li></ul></div>
    <div class="col-map"><h5>Our Location</h5><div class="map" role="img" aria-label="Street map showing the pharmacy location"></div></div>
    <div class="col-news"><h5>Newsletter</h5><p>Sign up for news and offers</p><div class="email">Email address</div><span class="btn subscribe">SUBSCRIBE</span></div>
  </div>
  <div class="footer-bottom">
    <span>© Larkfield Chemists. All rights reserved.</span>
    <div class="social"><span></span><span></span><span></span></div>
  </div>
</footer>
</body>
</html>
```